Business Cards for new orthopaedic surgery practice

My husband and I are starting our own orthopaedic surgery practice. We are looking for a business card that is uniform, but one will have my name/title and the other will have his. You can just create one design with my name on it for now. But when I choose your design as the winning design I will ask that you add another copy with his name/title.

We are looking for classy, simple, elite all in one. We like dark blues/a little gold/yellow. Something that goes with our logo. We want our logo incorporated. Here is all the info you need:
Business name: RV Bone & Vitality Center
Location: 38517 North Willowmere Ave
Palm Hollow, FL 33902
Phone: 954-218-4063
Fax: 954-582-7341
Email: info@myrvbonecare.example

Names: Lydia Vance, M.D.
Board Certified Hand and Upper Extremity Surgeon

Ebo Dansu, M.D.
Board Certified Hip & Knee Replacement/General Orthopaedic Surgeon

Can decide what you want to put on the back. Maybe a slogan:
Rooted in Care. Focused on You

I am just going to upload our logo. The only thing is if we select you as the winning design, the location, and phone numbers may change. We will need your help to update that once fully solidified.

Industry/Entity Type

Medical

Contact Information for Business Card

Colors
0054AA
0677BA
7BADD7
CADEEF
E8F1F8
0094D4
00A9DD
6FCCEA
C7EBF8
E9F6FB

Requirements
Must have
• class, appeal,
Should not have
• We want to air on the side of masculine if we are looking at masculine vs. feminine feel. But we still want it classy, sophisticated, and something we will love

```html
<!DOCTYPE html>
<html lang="en">
<head>
<meta charset="utf-8">
<title>RV Bone &amp; Vitality Center – Business Card</title>
<link href="https://fonts.googleapis.com/css2?family=Tinos:wght@400;700&display=swap" rel="stylesheet">
<style>
  :root {
    --navy: #1c2a4f;
    --gold: #c8a45e;
    --white: #ffffff;
    --backdrop: #e1e6e9;
  }
  * { margin: 0; padding: 0; box-sizing: border-box; }
  html, body { width: 1200px; height: 960px; overflow: hidden; }
  body {
    background: var(--backdrop);
    font-family: "Tinos", "Times New Roman", serif;
    position: relative;
  }
  .card {
    position: absolute;
    left: 248px;
    width: 704px;
    height: 402px;
    border-radius: 28px;
    overflow: hidden;
  }
  .card-front { top: 60px; background: var(--navy); }
  .card-back { top: 500px; background: var(--white); }

  .brand-seal {
    position: absolute;
    width: 200px; height: 200px;
    border-radius: 50%;
    border: 2px solid var(--gold);
    display: flex; align-items: center; justify-content: center;
    text-align: center;
    font-size: 24px; line-height: 1.2; font-weight: 400;
    letter-spacing: 1px;
  }
  .card-front .brand-seal { left: 252px; top: 90px; color: var(--white); }
  .card-back .brand-seal { left: 86px; top: 102px; color: var(--navy); }

  .tagline {
    position: absolute;
    left: 0; right: 0; top: 356px;
    text-align: center;
    color: var(--white);
    font-size: 17px;
    letter-spacing: 0.6px;
  }
  .tagline .dot {
    display: inline-block;
    width: 7px; height: 7px; border-radius: 50%;
    background: var(--gold);
    margin: 0 6px 2px 0;
  }
  .tagline .dot.second { margin-left: 8px; }

  .divider {
    position: absolute;
    left: 351px; top: 71px;
    width: 1px; height: 239px;
    background: var(--gold);
  }
  .person {
    position: absolute; left: 407px; top: 112px;
  }
  .person-name {
    color: var(--gold);
    font-weight: 700;
    font-size: 31px;
    letter-spacing: 1px;
    line-height: 1;
  }
  .person-title {
    color: var(--navy);
    font-size: 17px;
    margin-top: 5px;
    letter-spacing: 0.3px;
  }
  .contact-list {
    position: absolute; left: 407px; top: 198px;
    list-style: none;
  }
  .contact-list li {
    display: flex; align-items: center;
    height: 22.5px;
    color: var(--navy);
    font-size: 18px;
    letter-spacing: 0.4px;
  }
  .contact-list svg {
    width: 16px; height: 16px; margin-right: 10px;
    fill: none; stroke: var(--gold); stroke-width: 1.6;
  }
  .address-band {
    position: absolute; left: 0; top: 346px;
    width: 570px; height: 31px;
    background: var(--gold);
    color: var(--white);
    font-size: 16px;
    letter-spacing: 0.6px;
    display: flex; align-items: center; justify-content: center;
    padding-left: 90px;
  }
  .brand-band {
    position: absolute; left: 570px; top: 346px;
    width: 134px; height: 31px;
    background: var(--navy);
    color: var(--white);
    font-size: 11px;
    line-height: 1.15;
    letter-spacing: 0.3px;
    display: flex; align-items: center; justify-content: center;
    text-align: center;
  }
</style>
</head>
<body>

<section class="card card-front">
  <div class="brand-seal">RV Bone &amp;<br>Vitality Center</div>
  <p class="tagline"><span class="dot"></span>Steady in Skill <span class="dot second"></span>Centered on You</p>
</section>

<section class="card card-back">
  <div class="brand-seal">RV Bone &amp;<br>Vitality Center</div>
  <div class="divider"></div>

  <div class="person">
    <h1 class="person-name">Lydia Vance, M.D.</h1>
    <p class="person-title">Hand and Upper Extremity Surgery</p>
  </div>

  <ul class="contact-list">
    <li>
      <svg viewBox="0 0 16 16"><path d="M3 2l3 1 1 3-2 1c1 2 2 3 4 4l1-2 3 1 1 3-2 1C7 14 2 9 2 4z"/></svg>
      954-218-4063
    </li>
    <li>
      <svg viewBox="0 0 16 16"><rect x="2" y="6" width="12" height="8"/><rect x="5" y="2" width="6" height="4"/><path d="M5 9h2M9 9h2M5 11h2M9 11h2"/></svg>
      954-582-7341
    </li>
    <li>
      <svg viewBox="0 0 16 16"><circle cx="8" cy="8" r="6"/><ellipse cx="8" cy="8" rx="2.5" ry="6"/><path d="M2 8h12M3 5h10M3 11h10"/></svg>
      www.myrvbonecare.example
    </li>
    <li>
      <svg viewBox="0 0 16 16"><rect x="2" y="4" width="12" height="10"/><path d="M2 4l6 5 6-5"/></svg>
      info@myrvbonecare.example
    </li>
  </ul>

  <div class="address-band">38517 North Willowmere Ave Palm Hollow, FL 33902</div>
  <div class="brand-band">RV Bone &amp;<br>Vitality Center</div>
</section>

</body>
</html>
```